Stationery Design Project

I need a stationary design for our company. we are based in Houston, TX and we are called Mira Vell Lending. And we are wanting to brand our MoneyMendPlus program, which includes our tax preparation and restoration, credit repair service. Although our business offers other programs, we are interested in mainly focusing on The MoneyMendPlus program. We are looking for way to brand our ourselves and I believe that a great stationery design will help in achieving this goal. Our logo design is blue and light blue. the slogan is orange.

Industry/Entity Type

Business

Requirements
Must have
• Address: 30871 Calloway Ln. B-22
Houston, TX 75419
Tel. 555-318-6207
Fax 555-294-7153
www.miravelllending.example
info@miravelllending.example
Our Slogan: Happiness, Restored!

```html
<!DOCTYPE html>
<html lang="en">
<head>
<meta charset="utf-8">
<title>Mira Vell Lending – Business Cards</title>
<link rel="stylesheet" href="https://fonts.googleapis.com/css2?family=Source+Sans+3:wght@400;600&family=Tinos&family=Cinzel:wght@600&display=swap">
<style>
  :root {
    --backdrop: #7a5238;
    --label: #1a120c;
    --card-white: #ffffff;
    --navy: #123e66;
    --navy-deep: #0e3458;
    --brand-blue: #1d5f95;
    --band-light: #2a8fcf;
    --frame-light: #c9def0;
    --emblem-light: #4f8cc4;
    --emblem-dark: #2a5f92;
    --orange: #f2a23a;
    --ink: #333333;
    --white: #ffffff;
  }
  * { box-sizing: border-box; margin: 0; padding: 0; }
  html, body {
    width: 1200px; height: 800px; overflow: hidden;
    background: var(--backdrop);
  }
  .sheet { position: relative; width: 1200px; height: 800px; }
  .side-label {
    position: absolute; width: 508px; text-align: center;
    font: 400 22px "Source Sans 3", sans-serif; color: var(--label);
  }
  .card {
    position: absolute; width: 508px; height: 290px;
    border-radius: 22px; overflow: hidden;
    box-shadow: 0 4px 10px rgba(0,0,0,.35);
  }
  .card--white { background: var(--card-white); }
  .card--navy { background: var(--navy); }

  /* Emblem placeholder: one plain square beside the name */
  .emblem {
    position: absolute;
    background: linear-gradient(180deg, var(--emblem-light), var(--emblem-dark));
  }
  .emblem--front { left: 226px; top: 24px; width: 56px; height: 56px;
    background: linear-gradient(135deg, var(--band-light), var(--navy-deep)); }
  .emblem--tile { left: 227px; top: 70px; width: 54px; height: 54px; }
  .emblem--large { left: 212px; top: 52px; width: 84px; height: 84px; }
  .emblem--frame { left: 226px; top: 76px; width: 54px; height: 54px; }

  /* Front */
  .front-name {
    position: absolute; top: 82px; width: 100%; text-align: center;
    font: 600 40px "Source Sans 3", sans-serif; color: var(--brand-blue);
    letter-spacing: -0.5px;
  }
  .slogan-band {
    position: absolute; top: 160px; left: 0; width: 100%; height: 42px;
    background: linear-gradient(90deg, var(--navy-deep), var(--brand-blue) 55%, var(--band-light));
    border-top: 2px solid var(--orange); border-bottom: 2px solid var(--orange);
    display: flex; align-items: center; justify-content: center;
  }
  .slogan {
    font: 600 18px "Cinzel", serif; color: var(--orange); letter-spacing: 1px;
  }
  .contact {
    position: absolute; top: 210px; width: 100%;
    display: flex; justify-content: center; gap: 6px;
    font: 400 13.5px "Source Sans 3", sans-serif; color: var(--ink); line-height: 18px;
  }
  .contact__col--phones { text-align: right; padding-right: 6px; border-right: 1px solid var(--ink); }
  .address {
    position: absolute; top: 258px; width: 100%; text-align: center;
    font: 400 14px "Source Sans 3", sans-serif; color: var(--ink);
  }

  /* Backs */
  .brand-tile {
    position: absolute; left: 170px; top: 33px; width: 170px; height: 170px;
    background: var(--navy); border: 3px solid var(--frame-light);
  }
  .brand-frame {
    position: absolute; left: 168px; top: 35px; width: 170px; height: 170px;
    border: 4px solid var(--frame-light);
  }
  .brand-name {
    position: absolute; width: 100%; text-align: center;
    font: 400 15px "Tinos", serif; color: var(--white); white-space: nowrap;
  }
  .card--white .brand-name { top: 155px; }
  .card--navy .brand-frame + .brand-name { top: 157px; }
  .brand-name--large { top: 182px; font-size: 22px; }
  .web {
    position: absolute; width: 100%; text-align: center;
    font: 400 20px "Source Sans 3", sans-serif; letter-spacing: 1.8px;
  }
  .card--white .web { top: 236px; color: var(--ink); }
  .card--navy .web { top: 248px; color: var(--white); }
</style>
</head>
<body>
<main class="sheet">
  <div class="side-label" style="left:72px; top:50px;">Front</div>
  <section class="card card--white" style="left:72px; top:90px;">
    <div class="emblem emblem--front" role="img" aria-label="Program emblem area"></div>
    <div class="front-name">MoneyMendPlus</div>
    <div class="slogan-band"><span class="slogan">Happiness, Restored!</span></div>
    <div class="contact">
      <div class="contact__col--phones">p : 555-318-6207<br>f : 555-294-7153</div>
      <div>e : info@miravelllending.example<br>w : www.miravelllending.example</div>
    </div>
    <div class="address">30871 Calloway Ln. B-22, Houston, TX 75419</div>
  </section>

  <div class="side-label" style="left:622px; top:50px;">Back - 1</div>
  <section class="card card--white" style="left:622px; top:90px;">
    <div class="brand-tile"></div>
    <div class="emblem emblem--tile" role="img" aria-label="Company emblem area"></div>
    <div class="brand-name">Mira Vell Lending</div>
    <div class="web">www.miravelllending.example</div>
  </section>

  <div class="side-label" style="left:76px; top:410px;">Back - 2</div>
  <section class="card card--navy" style="left:76px; top:450px;">
    <div class="emblem emblem--large" role="img" aria-label="Company emblem area"></div>
    <div class="brand-name brand-name--large">Mira Vell Lending</div>
    <div class="web">www.miravelllending.example</div>
  </section>

  <div class="side-label" style="left:622px; top:410px;">Back - 3</div>
  <section class="card card--navy" style="left:622px; top:450px;">
    <div class="emblem emblem--frame" role="img" aria-label="Company emblem area"></div>
    <div class="brand-frame"></div>
    <div class="brand-name">Mira Vell Lending</div>
    <div class="web">www.miravelllending.example</div>
  </section>
</main>
</body>
</html>
```